Business Card Design needed - Something Awesome!

Need a business card designed. Company is "Marlowe Advisory" we do consulting and also have sales automation technology.
I'm going to use thick stock or metal, something really nice... I was thinking about a QR Code on the back that would just upload my contact info to the persons contact, etc -

This is a Strategy Company with a tech feel. I'm open to ideas but really want this to be nice!

I need a template that should include:

Name | Position or Title
D: 415.902.3376
www.marloweadvisory.example

I'm going to attach my contact so you can use that one, I need to get this printed.

Target Market(s)

Small to mid size customers, Entrepreneurs etc.

Industry/Entity Type

Consulting, Tech, Private Equity.

Contact Information for Business Card

Name, Phone, Maybe email, URL

Font styles to use
Sans Serif

Colors

Designer to choose only greyscale colors for use in the design.

Requirements
Must have
• Fresh, Clean, stand out from the crowd - will be on thick stock or metal.
Nice to have
• Clean, simple yet impactful.
Should not have
• Not cartoonish

```html
<!DOCTYPE html>
<html lang="en">
<head>
<meta charset="utf-8">
<title>Marlowe Advisory — Business Card</title>
<link href="https://fonts.googleapis.com/css2?family=Roboto:wght@300;400;700&display=swap" rel="stylesheet">
<style>
  :root {
    --backdrop: #2f2f2f;
    --card-black: #141414;
    --card-edge: #0a0a0a;
    --silver: #d4d4d4;
    --silver-dim: #a9a9a9;
    --rule: #6a6a6a;
    --pattern-dark: #0c0c0c;
    --pattern-mid: #262626;
    --pattern-light: #3a3a3a;
  }
  * { margin: 0; padding: 0; box-sizing: border-box; }
  html, body {
    width: 1200px; height: 801px; overflow: hidden;
    background: var(--backdrop);
    font-family: "Roboto", Arial, sans-serif;
  }
  .canvas {
    position: relative; width: 1200px; height: 801px;
    display: flex; align-items: center; justify-content: center; gap: 40px;
  }
  .card {
    position: relative; width: 530px; height: 303px;
    background: var(--card-black);
    border-radius: 3px;
    box-shadow: 0 2px 0 var(--card-edge), 0 18px 40px rgba(0,0,0,.45);
    overflow: hidden;
  }
  /* Front */
  .wordmark {
    position: absolute; left: 0; right: 0; top: 70px;
    text-align: center;
    font-weight: 300; font-size: 64px; letter-spacing: 6px;
    color: var(--silver);
  }
  .details {
    position: absolute; left: 0; right: 0; top: 190px;
    display: flex; justify-content: center; align-items: center;
  }
  .identity { text-align: right; padding-right: 22px; }
  .identity .person {
    font-weight: 700; font-size: 17px; letter-spacing: 1px;
    text-transform: uppercase; color: var(--silver);
  }
  .identity .role {
    margin-top: 4px; font-weight: 400; font-size: 14px; color: var(--silver-dim);
  }
  .divider { width: 1px; height: 60px; background: var(--rule); }
  .contact { list-style: none; padding-left: 22px; }
  .contact li {
    display: flex; align-items: center; gap: 8px;
    font-size: 13px; color: var(--silver); line-height: 20px;
  }
  .contact svg { width: 11px; height: 11px; flex: none; }
  /* Back */
  .back-field {
    position: absolute; inset: 0;
    background: linear-gradient(120deg, var(--pattern-dark) 0%, var(--pattern-mid) 55%, var(--pattern-light) 100%);
  }
  .back-name {
    position: absolute; left: 0; right: 0; top: 50%;
    transform: translateY(-50%);
    text-align: center;
    font-weight: 300; font-size: 30px; letter-spacing: 5px;
    color: var(--silver);
  }
</style>
</head>
<body>
<main class="canvas">
  <section class="card card-front" aria-label="Card front">
    <div class="wordmark">MARLOWE</div>
    <div class="details">
      <div class="identity">
        <div class="person">Dorian K. Hale</div>
        <div class="role">Founder / CEO</div>
      </div>
      <div class="divider"></div>
      <ul class="contact">
        <li>
          <svg viewBox="0 0 12 12" aria-hidden="true"><circle cx="6" cy="6" r="6" fill="var(--silver)"/><path d="M4 3.2l1 1.4-.6.7c.4.9 1 1.5 1.9 1.9l.7-.6 1.4 1-.6 1.2C5.8 8.6 3.4 6.2 3.2 3.8z" fill="var(--card-black)"/></svg>
          415.902.3376
        </li>
        <li>
          <svg viewBox="0 0 12 12" aria-hidden="true"><rect x="1" y="2.5" width="10" height="7" fill="var(--silver)"/><path d="M1 2.5l5 4 5-4" stroke="var(--card-black)" fill="none"/></svg>
          info@marloweadvisory.example
        </li>
        <li>
          <svg viewBox="0 0 12 12" aria-hidden="true"><circle cx="6" cy="6" r="5.5" fill="var(--silver)"/><ellipse cx="6" cy="6" rx="2.2" ry="5" fill="none" stroke="var(--card-black)" stroke-width=".8"/><path d="M1 6h10" stroke="var(--card-black)" stroke-width=".8"/></svg>
          www.marloweadvisory.example
        </li>
      </ul>
    </div>
  </section>

  <section class="card card-back" aria-label="Card back">
    <div class="back-field" role="img" aria-label="Gloss spot-varnish pattern of staggered squares on black"></div>
    <div class="back-name">MARLOWE</div>
  </section>
</main>
</body>
</html>
```